Danielle Brooke Interiors business cards

We need a DOUBLE SIDED business card design that is simple, elegant and modern. We are a rapidly growing Interior Design Firm, and our brand colours are blush pink, navy, and antique gold, so we require some or all of these colours to be used. The final design should portray elegance, simplicity, and have a modern feel. We have upload inspiration photos that have the feel we're looking for.

Industry/Entity Type

Interior Design

Contact Information for Business Card

Contact information and LOGO

Colors
EB3D1F
EC4F4E
F09395
F8D3D4
FCEDEE

Requirements
Must have
• Navy, the right shade of blush pink, and antique gold

```html
<!DOCTYPE html>
<html lang="en">
<head>
<meta charset="utf-8">
<title>Danielle Brooke Interiors – Business Cards</title>
<link rel="stylesheet" href="https://fonts.googleapis.com/css2?family=Jost:wght@400;500;600&family=Allura&display=swap">
<style>
  :root {
    --backdrop: #eeebe6;
    --blush: #eeaa98;
    --blush-deep: #e79a88;
    --cream: #f0e4c9;
    --navy: #1c1f45;
    --gold: #8a6328;
    --gold-soft: #dcc59c;
  }
  * { margin: 0; padding: 0; box-sizing: border-box; }
  html, body {
    width: 1200px; height: 800px; overflow: hidden;
    background: var(--backdrop);
    font-family: "Jost", sans-serif;
  }
  .sheet {
    position: relative; width: 1200px; height: 800px;
    display: flex; align-items: center; justify-content: center; gap: 70px;
  }
  .card {
    position: relative; width: 500px; height: 286px;
    box-shadow: 0 10px 30px rgba(60, 50, 40, 0.12);
    overflow: hidden;
  }

  /* Front */
  .card-front {
    background: linear-gradient(160deg, var(--blush) 0%, var(--blush-deep) 100%);
    display: flex; align-items: center; justify-content: center; gap: 14px;
  }
  .brand-mark { width: 18px; height: 18px; background: var(--navy); flex: none; }
  .brand-name {
    font-weight: 500; font-size: 26px; letter-spacing: 0.04em;
    color: var(--navy); text-transform: uppercase;
  }

  /* Back */
  .card-back { background: var(--cream); color: var(--navy); }
  .back-content { position: absolute; left: 30px; top: 28px; width: 300px; }
  .back-brand { display: flex; align-items: center; gap: 8px; margin-bottom: 14px; }
  .back-brand .brand-mark { width: 12px; height: 12px; }
  .back-brand .brand-name { font-size: 13px; }
  .person-name { font-weight: 600; font-size: 19px; letter-spacing: 0.06em; text-transform: uppercase; line-height: 1.1; }
  .person-role { font-size: 13px; margin-bottom: 12px; }
  .contact-list { list-style: none; font-size: 12.5px; line-height: 1.55; }
  .contact-list li { display: flex; align-items: center; gap: 8px; }
  .contact-list svg { width: 11px; height: 11px; fill: var(--navy); flex: none; }
  .social-heading {
    font-family: "Allura", cursive; font-size: 22px; color: var(--gold);
    margin-top: 10px; line-height: 1;
  }
  .social-list { list-style: none; font-size: 12px; color: var(--gold); line-height: 1.5; }
  .social-list li { display: flex; align-items: center; gap: 7px; }
  .social-dot { width: 8px; height: 8px; border-radius: 50%; background: var(--gold); flex: none; }
  .back-pattern {
    position: absolute; right: 0; top: 0; width: 170px; height: 100%;
    background: linear-gradient(180deg, var(--cream) 0%, var(--gold-soft) 100%);
  }
</style>
</head>
<body>
<main class="sheet">
  <section class="card card-front" aria-label="Business card front">
    <span class="brand-mark"></span>
    <span class="brand-name">Danielle Brooke Interiors</span>
  </section>

  <section class="card card-back" aria-label="Business card back">
    <div class="back-content">
      <div class="back-brand">
        <span class="brand-mark"></span>
        <span class="brand-name">Danielle Brooke Interiors</span>
      </div>
      <h1 class="person-name">Danielle Brooke</h1>
      <p class="person-role">Founder Director</p>
      <ul class="contact-list">
        <li><svg viewBox="0 0 24 24" aria-hidden="true"><path d="M6.6 10.8a15.1 15.1 0 0 0 6.6 6.6l2.2-2.2a1 1 0 0 1 1-.25 11.4 11.4 0 0 0 3.6.57 1 1 0 0 1 1 1V20a1 1 0 0 1-1 1A17 17 0 0 1 3 4a1 1 0 0 1 1-1h3.5a1 1 0 0 1 1 1c0 1.25.2 2.45.57 3.57a1 1 0 0 1-.25 1z"/></svg>905-555-0142</li>
        <li><svg viewBox="0 0 24 24" aria-hidden="true"><path d="M2 5h20v14H2z M4 7v.5l8 5 8-5V7l-8 5z" fill-rule="evenodd"/></svg>danielle@dbinteriorsinc.com</li>
        <li><svg viewBox="0 0 24 24" aria-hidden="true"><path d="M12 2a10 10 0 1 0 0 20 10 10 0 0 0 0-20zm0 2c.9 1.2 1.6 2.9 1.9 5h-3.8c.3-2.1 1-3.8 1.9-5zM4.3 11h3.8c.1 1.1.2 2.1.5 3H5a8 8 0 0 1-.7-3zm5.8 0h3.8c0 1.1-.2 2.1-.4 3h-3c-.2-.9-.4-1.9-.4-3zm5.8 0h3.8a8 8 0 0 1-.7 3h-3.6c.3-.9.4-1.9.5-3z"/></svg>www.daniellebrookeinteriors.com</li>
      </ul>
      <p class="social-heading">Find her online</p>
      <ul class="social-list">
        <li><span class="social-dot"></span>daniellebrookeinteriors</li>
        <li><span class="social-dot"></span>danielle.brooke.interiors</li>
      </ul>
    </div>
    <div class="back-pattern" role="img" aria-label="Antique gold geometric line pattern"></div>
  </section>
</main>
</body>
</html>
```